Website Redesign for Brightvale Forgeworks

We are looking for a high-end Minimalist Design That will give potential customers the feel that they are purchasing a hand-crafted reproduction of an actual historical medieval sword. The tone or feel should like a luxury sword manufacturer.
Perhaps having a darker background with logo/text that pops more with a white glow.

Target Market(s)

Historical "efficinato" - educated history buffs interested in high end swords & armors, with a available capital for such a hobby.

Number of Pages Required

3 page

Font styles to use
Serif

Colors
1b1b1b
000000
e6e6e6
c9c9c9

Requirements
Must have
• -cart page
• -home page
• -1 product page
Nice to have
• -large images
• - Garamon or Centaur font
• - Our logo is in Trojan Pro
Should not have
• -no excessive use of colors
• -no medieval / gothic fonts

```html
<!DOCTYPE html>
<html lang="en">
<head>
<meta charset="utf-8">
<title>Brightvale Forgeworks — Medieval Swords</title>
<link href="https://fonts.googleapis.com/css2?family=Cinzel:wght@400;600&family=EB+Garamond:wght@400;500;600&family=Lato:wght@400;700&display=swap" rel="stylesheet">
<style>
:root{
  --ink:#000000;
  --coal:#1b1b1b;
  --panel:#222222;
  --mist:#e6e6e6;
  --silver:#c9c9c9;
  --muted:#9a9a9a;
  --line:#3a3a3a;
  --white:#ffffff;
}
*{box-sizing:border-box;margin:0;padding:0}
html,body{width:1200px;height:3742px;overflow:hidden;background:var(--ink)}
body{position:relative;font-family:"Lato",Arial,sans-serif;color:var(--mist)}
section,header,nav,footer{position:absolute;left:0;width:1200px}

/* top bar */
.topbar{top:0;height:55px;background:var(--coal)}
.social{position:absolute;left:70px;top:12px;display:flex;gap:11px}
.social span{width:31px;height:31px;border-radius:50%;border:2px solid #8a8a8a;display:block}
.contact{position:absolute;right:72px;top:0;height:55px;display:flex;align-items:center;gap:16px;font-size:17px;color:var(--mist);letter-spacing:.5px}
.contact svg{display:block}
.sep{color:#777}

/* nav */
.navbar{top:55px;height:140px;background:var(--ink)}
.brand{position:absolute;left:75px;top:42px;display:flex;align-items:center;gap:14px;font-family:"EB Garamond",Georgia,serif;font-size:27px;font-weight:500;color:var(--white);line-height:1.05}
.brand i{width:48px;height:48px;border-radius:50%;background:var(--white);display:block}
.menu{position:absolute;left:410px;top:0;height:140px;display:flex;align-items:center;gap:34px;font-family:"EB Garamond",Georgia,serif;font-weight:600;font-size:18px;color:var(--white)}

/* hero */
.hero{top:195px;height:496px;background:linear-gradient(135deg,#5a4a3a 0%,#2e2620 30%,#8c8478 55%,#3a3028 80%,#6a5c4c 100%)}
.hero-box{position:absolute;left:262px;top:124px;width:681px;height:192px;background:rgba(0,0,0,.55);border:2px solid rgba(255,255,255,.5);text-align:center;padding-top:14px}
.hero-box h1{font-family:"Cinzel",Georgia,serif;font-weight:600;font-size:58px;letter-spacing:2px;color:var(--white);line-height:1}
.hero-box p{font-family:"EB Garamond",Georgia,serif;font-size:25px;line-height:1.28;color:var(--white);margin-top:12px}
.arrow{position:absolute;width:30px;height:40px}

/* intro */
.intro{top:691px;height:601px;background:linear-gradient(180deg,#2a2219 0%,#1c1712 60%,#141210 100%);text-align:center}
.intro h2{position:absolute;left:0;width:1200px;top:140px;font-family:"EB Garamond",Georgia,serif;font-weight:500;font-size:48px;line-height:1.15;color:var(--white)}
.intro p{position:absolute;left:175px;width:850px;top:266px;font-size:14.5px;line-height:1.9;color:var(--silver)}
.btn{position:absolute;border:2px solid var(--mist);color:var(--white);font-family:"EB Garamond",Georgia,serif;font-size:17px;letter-spacing:1.5px;display:flex;align-items:center;justify-content:center}
.intro .btn{left:497px;top:400px;width:207px;height:58px}

/* newsletter */
.newsletter{top:1292px;height:208px;background:var(--ink)}
.newsletter h2{position:absolute;top:35px;width:1200px;text-align:center;font-family:"EB Garamond",Georgia,serif;font-weight:500;font-size:40px;color:var(--white)}
.email{position:absolute;left:342px;top:110px;width:334px;height:53px;border:2px solid var(--silver);font-size:12px;color:var(--white);padding:17px 14px}
.signup{position:absolute;left:694px;top:110px;width:162px;height:53px;background:var(--panel);color:var(--white);font-family:"EB Garamond",Georgia,serif;font-size:19px;letter-spacing:2px;display:flex;align-items:center;justify-content:center}

/* feature splits */
.split{height:507px;background:var(--coal)}
.split-1{top:1500px}
.split-2{top:2007px}
.photo{position:absolute;top:0;height:507px;width:601px}
.split-1 .photo{left:0;background:linear-gradient(135deg,#4a3524 0%,#6b5a44 40%,#7d7d7a 65%,#3c3c3a 100%)}
.split-2 .photo{left:601px;background:linear-gradient(135deg,#151515 0%,#4a4a4a 45%,#9a9a9a 60%,#2a2a2a 100%)}
.copy{position:absolute;top:0;width:540px}
.split-1 .copy{left:633px;top:70px}
.split-2 .copy{left:75px;top:68px;width:500px}
.copy h3{font-family:"EB Garamond",Georgia,serif;font-weight:500;font-size:34px;line-height:1.3;color:var(--white)}
.copy p{font-size:14.5px;line-height:1.95;color:var(--silver);margin-top:26px}

/* videos */
.videos{top:2514px;height:505px;background:var(--ink)}
.videos h2{position:absolute;top:40px;width:1200px;text-align:center;font-family:"EB Garamond",Georgia,serif;font-weight:500;font-size:40px;color:var(--white)}
.video{position:absolute;top:126px;width:479px;height:334px;display:flex;align-items:center;justify-content:center}
.video-a{left:107px;background:linear-gradient(160deg,#b5b2a8 0%,#6d6a62 50%,#3a3833 100%)}
.video-b{left:614px;background:linear-gradient(160deg,#8d8a82 0%,#5b5852 50%,#2f2d29 100%)}
.play{width:62px;height:44px;background:var(--white);border-radius:9px;display:flex;align-items:center;justify-content:center}

/* tiles */
.tiles{top:3019px;height:412px;background:var(--coal)}
.tile{position:absolute;top:42px;width:339px;height:300px;display:flex;align-items:center;justify-content:center;font-family:"EB Garamond",Georgia,serif;font-weight:600;font-size:34px;color:var(--white)}
.tile-a{left:75px;background:linear-gradient(135deg,#3a3a3a,#6e6458 60%,#2a2a2a)}
.tile-b{left:432px;background:linear-gradient(135deg,#2c3544,#4a5668 55%,#2a2a30)}
.tile-c{left:786px;background:linear-gradient(135deg,#6a6e62,#8c8a80 50%,#4a5a3a)}

/* footer */
.footer{top:3431px;height:311px;background:var(--ink)}
.col{position:absolute;top:30px}
.col h4{font-family:"EB Garamond",Georgia,serif;font-weight:500;font-size:19px;letter-spacing:1.5px;color:var(--white);margin-bottom:6px}
.col ul{list-style:none}
.col li{font-size:13.5px;line-height:26.6px;color:var(--silver)}
.col-company{left:75px}
.col-products{left:286px}
.col-more{left:532px;top:62px}
.foot-brand{position:absolute;left:852px;top:60px;display:flex;align-items:center;gap:12px;font-family:"EB Garamond",Georgia,serif;font-weight:500;font-size:24px;color:var(--white);line-height:1.05}
.foot-brand i{width:42px;height:42px;border-radius:50%;background:var(--white);display:block}
.badge{position:absolute;left:882px;top:170px;width:82px;height:42px;background:var(--mist);border-radius:3px}
.copyright{position:absolute;left:0;bottom:0;width:1200px;height:40px;background:var(--coal);text-align:center;font-size:11px;line-height:40px;color:var(--muted)}
</style>
</head>
<body>

<header class="topbar">
  <div class="social" aria-label="Social links"><span></span><span></span><span></span><span></span><span></span></div>
  <div class="contact">
    <svg width="18" height="18" viewBox="0 0 24 24" aria-hidden="true"><path fill="#e6e6e6" d="M6.6 10.8a15.1 15.1 0 0 0 6.6 6.6l2.2-2.2c.3-.3.7-.4 1-.2 1.1.4 2.3.6 3.6.6.6 0 1 .4 1 1V20c0 .6-.4 1-1 1A17 17 0 0 1 3 4c0-.6.4-1 1-1h3.5c.6 0 1 .4 1 1 0 1.3.2 2.5.6 3.6.1.3 0 .7-.2 1z"/></svg>
    <span>555.014.2290</span><span class="sep">|</span><span>1.800.555.0137</span>
    <svg width="18" height="18" viewBox="0 0 24 24" aria-hidden="true" style="margin-left:14px"><circle cx="10" cy="10" r="6.5" fill="none" stroke="#e6e6e6" stroke-width="2.5"/><path d="M15 15l6 6" stroke="#e6e6e6" stroke-width="2.8"/></svg>
    <span class="sep">|</span>
    <svg width="20" height="18" viewBox="0 0 24 22" aria-hidden="true"><path fill="#e6e6e6" d="M1 2h4l3 12h12l3-9H7" stroke="#e6e6e6" stroke-width="1.5"/><circle cx="9" cy="19" r="2" fill="#e6e6e6"/><circle cx="19" cy="19" r="2" fill="#e6e6e6"/></svg>
    <span>(0)</span>
  </div>
</header>

<nav class="navbar">
  <div class="brand"><i></i><span>Brightvale<br>Forgeworks</span></div>
  <div class="menu">
    <span>Medieval Swords</span><span>Armors</span><span>Daggers</span><span>Axes</span><span>Viking Jewelry</span><span>Blog</span><span>SALE ITEMS</span>
  </div>
</nav>

<section class="hero" role="img" aria-label="Close-up of ornate sword hilts and pommels on a wooden table">
  <div class="hero-box">
    <h1>MEDIEVAL SWORDS</h1>
    <p>Retailers &amp; wholesale distributors of Hand Forged<br>Battle Ready Medieval Swords &amp; Armors for<br>serious collectors and practitioners..</p>
  </div>
  <svg class="arrow" style="left:68px;top:190px" viewBox="0 0 30 40"><path d="M22 4L6 20l16 16" fill="none" stroke="#fff" stroke-width="5"/></svg>
  <svg class="arrow" style="left:1100px;top:190px" viewBox="0 0 30 40"><path d="M8 4l16 16L8 36" fill="none" stroke="#fff" stroke-width="5"/></svg>
</section>

<section class="intro" role="img" aria-label="Dim background of a sword and a certificate on a dark table">
  <h2>Medieval Swords, Battle Ready Swords,<br>Daggers &amp; Armors</h2>
  <p>Brightvale Forgeworks's battle ready Medieval swords, daggers and medieval weapons are individually hand forged in Canada to look, feel and handle as the originals. Each sword is recreated from Museum originals and antiques, using the finest material and forged with 5160 High Carbon steel, properly heat treated and Tempered.</p>
  <div class="btn">SEE PORTFOLIO</div>
</section>

<section class="newsletter">
  <h2>Newsletter Signup</h2>
  <div class="email">Enter Email Address</div>
  <div class="signup">SIGN UP</div>
</section>

<section class="split split-1">
  <div class="photo" role="img" aria-label="Ornate sword hilt resting on chainmail over a wooden surface"></div>
  <div class="copy">
    <h3>Battle-Ready Medieval Swords,<br>Medieval Weapons,<br>Armors &amp; European<br>Reenactment Weapons</h3>
    <p>Our blade-smiths individually handcraft each medieval sword using the traditional techniques of the middle ages (Hammer &amp; Anvil) while remaining true to size, weight, and geometry. This ultimately produces a sword that feels and looks authentic, as the originals and made as fully functional battle ready weapon.</p>
  </div>
</section>

<section class="split split-2">
  <div class="copy">
    <h3>Medieval Weapons &amp;<br>European<br>Reenactment Weapons</h3>
    <p>Through painstaking research and first-hand experience with antique medieval weapons, Brightvale Forgeworks has crafted truly functional medieval swords able to withstand the rigors of combat. Our swords are finely crafted in a traditional and authentic manner, as those of the middle ages. Our Medieval weapons are sold either blunt for safety, or sharp for cutting tests.</p>
  </div>
  <div class="photo" role="img" aria-label="Steel gauntlet and sword lying on chainmail in black and white"></div>
</section>

<section class="videos">
  <h2>Watch Videos</h2>
  <svg class="arrow" style="left:55px;top:276px" viewBox="0 0 30 40"><path d="M22 4L6 20l16 16" fill="none" stroke="#fff" stroke-width="5"/></svg>
  <div class="video video-a" role="img" aria-label="Video still of a smith flexing a blade in the workshop"><div class="play"><svg width="22" height="24" viewBox="0 0 22 24"><path d="M2 1l19 11L2 23z" fill="#000"/></svg></div></div>
  <div class="video video-b" role="img" aria-label="Video still of a craftsman working at the forge"><div class="play"><svg width="22" height="24" viewBox="0 0 22 24"><path d="M2 1l19 11L2 23z" fill="#000"/></svg></div></div>
  <svg class="arrow" style="left:1114px;top:276px" viewBox="0 0 30 40"><path d="M8 4l16 16L8 36" fill="none" stroke="#fff" stroke-width="5"/></svg>
</section>

<section class="tiles">
  <div class="tile tile-a" role="img" aria-label="Recently finished sword on a dark surface">Most Recent</div>
  <div class="tile tile-b" role="img" aria-label="Swords displayed in the shop">Shop Pictures</div>
  <div class="tile tile-c" role="img" aria-label="Two sword practitioners sparring outdoors">Blog Posts</div>
</section>

<footer class="footer">
  <div class="col col-company">
    <h4>COMPANY</h4>
    <ul><li>About</li><li>Customer Reviews</li><li>Portfolio</li><li>F.A.Q</li><li>Ordering</li><li>Video</li><li>Contact</li></ul>
  </div>
  <div class="col col-products">
    <h4>PRODUCTS</h4>
    <ul><li>Medieval Swords</li><li>Crown Series</li><li>Medieval Daggers</li><li>Medieval Armor</li><li>Vanguard Series Medieval Weapons</li><li>Accessories</li><li>Battle axes</li></ul>
  </div>
  <div class="col col-more">
    <ul><li>HEMA, WMA Swords and Weapons</li><li>Viking Jewelry</li><li>On Sale</li></ul>
  </div>
  <div class="foot-brand"><i></i><span>Brightvale<br>Forgeworks</span></div>
  <div class="badge" aria-label="Security badge"></div>
  <div class="copyright">Copyright © 2016, Company Name All Right Reserved</div>
</footer>

</body>
</html>
```